Tech business card design

We need an amazing business card design for our new business 'Pexla' a marketing tech startup based in Sydney, Australia. We provide an online marketplace for businesses to search and buy advertising media, connect with service providers and learn more about marketing. We wish to communicate 'cool tech', reliability and professionalism and design based around our logo.

Target Market(s)

Business Owners

Contact Information for Business Card

Name
Position
Email Address
Website
Phone Number

Font styles to use
Other font styles liked:
• Avenir & Avenir Next

Colors

Designer to choose colors to be used in the design.

```html
<!DOCTYPE html>
<html lang="en">
<head>
<meta charset="utf-8">
<title>Pexla Business Card</title>
<link rel="stylesheet" href="https://fonts.googleapis.com/css2?family=Nunito+Sans:wght@400;600;800&display=swap">
<style>
  :root {
    --page-bg: #e6e6e6;
    --card-white: #ffffff;
    --navy: #14133b;
    --navy-soft: #1a1945;
    --text-grey: #555559;
    --title-grey: #6a6a70;
    --white: #ffffff;
  }
  * { box-sizing: border-box; margin: 0; padding: 0; }
  html, body {
    width: 1125px;
    height: 1200px;
    overflow: hidden;
    background: var(--page-bg);
    font-family: "Nunito Sans", "Avenir Next", Avenir, sans-serif;
  }
  .card {
    position: absolute;
    left: 171px;
    width: 826px;
    height: 471px;
    overflow: hidden;
  }
  .card--front { top: 106px; background: var(--card-white); }
  .card--back { top: 639px; background: var(--navy); }

  .front-wordmark {
    position: absolute;
    left: 50px;
    top: 40px;
    font-size: 140px;
    font-weight: 800;
    letter-spacing: -3px;
    line-height: 1;
    color: var(--navy);
  }

  .contact-list {
    position: absolute;
    left: 52px;
    top: 340px;
    list-style: none;
    font-size: 18.5px;
    color: var(--text-grey);
  }
  .contact-list li {
    display: flex;
    align-items: center;
    height: 26.5px;
  }
  .contact-list svg {
    width: 16px;
    height: 16px;
    margin-right: 11px;
    flex: none;
  }

  .person {
    position: absolute;
    right: 48px;
    top: 356px;
    text-align: right;
  }
  .person-name {
    font-size: 28px;
    font-weight: 600;
    color: var(--navy);
    line-height: 1.1;
  }
  .person-title {
    font-size: 20px;
    font-weight: 400;
    color: var(--title-grey);
    line-height: 1.3;
  }

  .back-texture {
    position: absolute;
    inset: 0;
    background: linear-gradient(160deg, var(--navy-soft) 0%, var(--navy) 100%);
  }

  .back-wordmark {
    position: absolute;
    right: 56px;
    bottom: 52px;
    font-size: 78px;
    font-weight: 800;
    letter-spacing: -1px;
    line-height: 1;
    color: var(--white);
  }
</style>
</head>
<body>

<section class="card card--front">
  <div class="front-wordmark">pexla</div>

  <ul class="contact-list">
    <li>
      <svg viewBox="0 0 16 16" aria-hidden="true"><rect x="3.5" y="1" width="9" height="14" rx="1.2" fill="none" stroke="#14133b" stroke-width="1.8"/><rect x="6.5" y="12" width="3" height="1.2" fill="#14133b"/></svg>
      +61 (0)412 555 018
    </li>
    <li>
      <svg viewBox="0 0 16 16" aria-hidden="true"><rect x="1" y="3.5" width="14" height="9" fill="#14133b"/><path d="M1.5 4 L8 9 L14.5 4" fill="none" stroke="#ffffff" stroke-width="1.2"/></svg>
      marcus@pexlamedia.com.au
    </li>
    <li>
      <svg viewBox="0 0 16 16" aria-hidden="true"><circle cx="8" cy="8" r="7" fill="#14133b"/><path d="M5 4.5 Q7 6 6 8 Q4.5 9.5 6 12 M10 3.5 Q9 6 11 7.5 Q12.5 9 11 11" fill="none" stroke="#ffffff" stroke-width="1.2"/></svg>
      www.pexlamedia.com.au
    </li>
  </ul>

  <div class="person">
    <p class="person-name">MARCUS DANE</p>
    <p class="person-title">FOUNDER, DIRECTOR</p>
  </div>
</section>

<section class="card card--back">
  <div class="back-texture" role="img" aria-label="Faint tone-on-tone repeated brand-name pattern covering the card back"></div>
  <div class="back-wordmark">pexla</div>
</section>

</body>
</html>
```